Halvery Construction Group Website

Need a dynamic corporate website that can be built on with time. We want to get our information out to the world and have a place where customers can submit requests for proposals.

Target Market(s)

Custom home owners and buyers. Architects and Real Estate Agents.

Industry/Entity Type

Construction

Number of Pages Required

3 page

Font styles to use
Serif
Sans Serif

Requirements
Must have
• Company logo, about, company contact information, biography, contact, projects,
• Sleek, modern, clean, attractive design.
• Online form customers can use for filling out a request for project proposal.
• Linkedin hyperlink.
• Uses www.halveryconstructiongroup.example

```html
<!DOCTYPE html>
<html lang="en">
<head>
<meta charset="utf-8">
<title>Halvery Construction Group</title>
<link href="https://fonts.googleapis.com/css2?family=Questrial&family=Open+Sans:ital,wght@0,400;0,600;0,700;1,600&display=swap" rel="stylesheet">
<style>
  :root{
    --blue:#0d5aa7;
    --blue-dark:#0a4a8c;
    --ink:#333;
    --muted:#666;
    --pale:#f4f7fa;
    --footer:#231f20;
    --footer-bottom:#1b1b1b;
    --white:#fff;
    --grey-btn:#5a5a5a;
  }
  *{margin:0;padding:0;box-sizing:border-box}
  html,body{width:910px;height:1200px;overflow:hidden;background:var(--white)}
  body{position:relative;font-family:"Open Sans",sans-serif;color:var(--ink)}
  .display{font-family:"Questrial",sans-serif}

  .top-rule{position:absolute;top:0;left:0;width:910px;height:2px;background:var(--blue)}
  .site-header{position:absolute;top:2px;left:0;width:910px;height:75px;background:var(--white)}
  .brand{position:absolute;left:74px;top:18px;display:flex;align-items:center;gap:8px}
  .brand-square{width:44px;height:42px;background:var(--blue)}
  .brand-name{font-family:"Questrial",sans-serif;color:var(--blue);font-size:27px;line-height:1;letter-spacing:.5px}
  .main-nav{position:absolute;top:32px;left:456px;display:flex;gap:0}
  .main-nav a{font-family:"Questrial",sans-serif;font-size:10px;color:var(--ink);text-decoration:none;margin-right:36px}
  .main-nav a.active{color:var(--blue)}
  .search-btn{position:absolute;left:812px;top:28px;width:23px;height:23px;border-radius:50%;background:#8a8a8a;display:flex;align-items:center;justify-content:center}

  .hero{position:absolute;top:77px;left:0;width:910px;height:368px;background:linear-gradient(180deg,#3d3f47 0%,#5b5548 35%,#3b3d42 70%,#2a2c30 100%)}
  .hero-title{position:absolute;top:124px;width:100%;text-align:center;color:var(--white);font-size:25px;letter-spacing:.3px}
  .hero-sub{position:absolute;top:158px;width:100%;text-align:center;color:var(--white);font-size:12.5px;line-height:22px}
  .hero-arrows{position:absolute;top:221px;left:430px;display:flex;gap:6px}
  .hero-arrows span{width:23px;height:20px;border:1px solid var(--white);display:flex;align-items:center;justify-content:center}

  .about{position:absolute;top:445px;left:0;width:910px;height:239px;text-align:center}
  .section-title{font-family:"Questrial",sans-serif;color:var(--blue);font-size:21px}
  .about .section-title{margin-top:28px}
  .about p{font-size:8.4px;color:var(--muted);line-height:17.6px;width:730px;margin:6px auto 0}
  .about p + p{margin-top:6px}
  .btn-row{display:flex;justify-content:center;gap:5px;margin-top:16px}
  .btn{font-family:"Questrial",sans-serif;font-size:9.5px;color:var(--white);height:35px;display:flex;align-items:center;justify-content:center}
  .btn-primary{width:103px;background:linear-gradient(var(--blue),var(--blue-dark))}
  .btn-secondary{width:102px;background:linear-gradient(#6a6a6a,#4c4c4c)}

  .projects-intro{position:absolute;top:684px;left:0;width:910px;height:117px;background:var(--pale);text-align:center}
  .projects-intro .section-title{margin-top:32px}
  .projects-intro p{font-size:8.4px;color:var(--muted);line-height:18px;width:600px;margin:4px auto 0}

  .project-grid{position:absolute;top:801px;left:0;width:910px;height:245px;display:flex;border-bottom:2px solid var(--blue)}
  .project-card{width:455px;height:243px;text-align:center;color:var(--white)}
  .project-card.blue{background:linear-gradient(135deg,#2a6fb8,#1b5ea8 60%,#2466ad)}
  .project-card.dark{background:linear-gradient(180deg,#3c4048,#4a4a48 60%,#2f3034)}
  .project-card h3{font-family:"Questrial",sans-serif;font-weight:400;font-size:11.5px;margin-top:67px}
  .project-card .date{font-style:italic;font-weight:600;font-size:8.5px;margin-top:6px}
  .project-card p{font-size:8.3px;line-height:16px;width:275px;margin:6px auto 0}
  .view-more{display:inline-block;margin-top:9px;width:75px;height:29px;border:1.5px solid var(--white);font-family:"Questrial",sans-serif;font-size:9.5px;line-height:26px}

  .site-footer{position:absolute;top:1046px;left:0;width:910px;height:115px;background:var(--footer);color:var(--white)}
  .footer-brand{position:absolute;left:74px;top:30px;display:flex;align-items:center;gap:8px}
  .footer-brand .brand-square{background:var(--white)}
  .footer-brand .brand-name{color:var(--white)}
  .footer-col-title{position:absolute;font-family:"Questrial",sans-serif;font-size:11.5px;top:30px}
  .contact-lines{position:absolute;top:56px;font-size:8.3px;line-height:15.5px}
  .email-field{position:absolute;left:600px;top:54px;width:160px;height:30px;background:var(--white);color:#888;font-size:8.5px;padding-left:10px;line-height:30px}
  .subscribe{position:absolute;left:766px;top:54px;width:69px;height:30px;background:var(--blue);font-weight:700;font-size:9.5px;letter-spacing:.4px;text-align:center;line-height:30px}

  .footer-bar{position:absolute;top:1161px;left:0;width:910px;height:39px;background:var(--footer-bottom);color:#9a9a9a;font-size:8.3px}
  .copyright{position:absolute;left:74px;top:14px}
  .social{position:absolute;left:667px;top:9px;display:flex;align-items:center;gap:2px}
  .social span{margin-right:6px}
  .social i{display:block;width:21px;height:21px;border:1.5px solid var(--white);border-radius:50%}
</style>
</head>
<body>
  <div class="top-rule"></div>

  <header class="site-header">
    <div class="brand"><div class="brand-square"></div><div class="brand-name">HALVERY</div></div>
    <nav class="main-nav">
      <a class="active" href="#">HOME</a><a href="#">ABOUT</a><a href="#">BIO</a><a href="#">PROJECTS</a><a href="#">CONTACT US</a>
    </nav>
    <div class="search-btn">
      <svg width="9" height="9" viewBox="0 0 10 10"><circle cx="4" cy="4" r="3" fill="none" stroke="#fff" stroke-width="1.5"/><line x1="6.2" y1="6.2" x2="9" y2="9" stroke="#fff" stroke-width="1.5"/></svg>
    </div>
  </header>

  <section class="hero" role="img" aria-label="City skyline with construction cranes and towers at dusk">
    <h1 class="hero-title display">HALVERY CONSTRUCTION GROUP</h1>
    <p class="hero-sub display">Nemo enim ipsam voluptatem quia voluptas sit aspernatur aut<br>odit aut fugit, sed quia consequuntur magni dolores...</p>
    <div class="hero-arrows">
      <span><svg width="8" height="8" viewBox="0 0 8 8"><path d="M5.5 1 2.5 4 5.5 7" fill="none" stroke="#fff" stroke-width="1.6"/></svg></span>
      <span><svg width="8" height="8" viewBox="0 0 8 8"><path d="M2.5 1 5.5 4 2.5 7" fill="none" stroke="#fff" stroke-width="1.6"/></svg></span>
    </div>
  </section>

  <section class="about">
    <h2 class="section-title">ABOUT TO HALVERY CONSTRUCTION GROUP</h2>
    <p>Nemo enim ipsam voluptatem quia voluptas sit aspernatur aut odit aut fugit, sed quia consequuntur magni dolores eos qui ratione voluptatem sequi nesciunt. Neque porro quisquam est, qui dolorem ipsum quia dolor sit amet, consectetur, adipisci velit, sed quia non numquam eius modi tempora incidunt ut labore et dolore magnam aliquam quaerat voluptatem. minima veniam, quis nostrum exercitationem ullam corporis suscipit laboriosam, nisi ut aliquid...</p>
    <p>Lemo enim ipsam voluptatem quia voluptas sit aspernatur aut odit aut fugit, sed quia consequuntur magni dolores eos qui ratione voluptatem sequi nesciunt. Neque porro quisquam qui dolorem rat voluptatem. minima veniam, quis nostrum exercitationem ullam corporis suscipit laboriosam, nisi ut aliquid...</p>
    <div class="btn-row">
      <a class="btn btn-primary">READ MORE INFO</a>
      <a class="btn btn-secondary">GET START TODAY</a>
    </div>
  </section>

  <section class="projects-intro">
    <h2 class="section-title">PROJECTS</h2>
    <p>Nemo enim ipsam voluptatem quia voluptas sit aspernatur aut odit aut fugit, sed quia consequuntur magni dolores eos qui ratione voluptatem sequi sed quia non numquam eius modi tempora incidunt ut labore et dolore magnam aliquam quaerat voluptatem.</p>
  </section>

  <section class="project-grid">
    <article class="project-card blue" role="img" aria-label="Office towers and crane under a blue tint">
      <h3>NEMO ENIM IPSAM VOLUPTATEM</h3>
      <div class="date">August 28, 2016</div>
      <p>Nemo enim ipsam voluptatem quia voluptas sit aspernatur aut odit aut fugit, sed quia consequuntur magni dolores...</p>
      <span class="view-more">View More</span>
    </article>
    <article class="project-card dark" role="img" aria-label="Pedestrian bridge leading to city towers">
      <h3>NEMO ENIM IPSAM VOLUPTATEM</h3>
      <div class="date">August 28, 2016</div>
      <p>Nemo enim ipsam voluptatem quia voluptas sit aspernatur aut odit aut fugit, sed quia consequuntur magni dolores...</p>
      <span class="view-more">View More</span>
    </article>
  </section>

  <footer class="site-footer">
    <div class="footer-brand"><div class="brand-square"></div><div class="brand-name">HALVERY</div></div>
    <h4 class="footer-col-title" style="left:305px">CONTACT US</h4>
    <div class="contact-lines" style="left:305px"># lorem ipsum Dummy<br>Text mcg lorem</div>
    <div class="contact-lines" style="left:419px">(000)-555-0142<br>info@halveryconstructiongroup.example</div>
    <h4 class="footer-col-title" style="left:600px">NEWSLETTER</h4>
    <div class="email-field">Email:</div>
    <div class="subscribe">SUBSCRIBE</div>
  </footer>

  <div class="footer-bar">
    <div class="copyright">© 2016 . halveryconstructiongroup | Allrights Reserved.</div>
    <div class="social"><span>Connect With Us :</span><i aria-label="Social link"></i><i aria-label="Social link"></i><i aria-label="Social link"></i><i aria-label="Social link"></i></div>
  </div>
</body>
</html>
```